Business IT Services Billboard to attract local small businesses

We are Brivoqua, a premier Managed Service Provider (MSP) specializing in comprehensive IT services and VOIP phone solutions exclusively for businesses. Our goal is to create a dynamic and visually engaging billboard advertisement that not only highlights our cutting-edge IT solutions but also emphasizes our state-of-the-art VOIP phone services. This billboard should communicate our commitment to providing innovative, reliable, and holistic technology solutions.
See the attached supporting documentation.
Target Market(s)
small business
Industry/Entity Type
Information Technology
Colors
Designer to choose colors to be used in the design.
Look and feel
Each slider illustrates characteristics of the customer's brand and the style your logo design should communicate.

```html
<!DOCTYPE html>
<html lang="en">
<head>
<meta charset="utf-8">
<title>Brivoqua – IT and VOIP Billboard</title>
<link rel="stylesheet" href="https://fonts.googleapis.com/css2?family=Montserrat:wght@600;700;800&family=Oswald:wght@600;700&display=swap">
<style>
  :root {
    --page-bg: #d4d4d4;
    --white: #ffffff;
    --brand-blue: #1569b3;
    --band-blue-dark: #0f4f8c;
    --navy: #0e2746;
    --navy-mid: #143a6b;
    --orange: #f7830f;
    --orange-dark: #e95a0c;
    --ink: #1b1b1b;
    --photo-light: #c9d6ea;
    --photo-mid: #7f98c4;
    --photo-deep: #2c3f7d;
  }
  * { margin: 0; padding: 0; box-sizing: border-box; }
  html, body {
    width: 1185px; height: 1200px; overflow: hidden;
    background: radial-gradient(ellipse at center, #e6e6e6 0%, var(--page-bg) 70%);
    font-family: "Montserrat", Arial, sans-serif;
  }
  .billboard {
    position: absolute; left: 40px; top: 439px;
    width: 1105px; height: 322px;
    box-shadow: 0 22px 30px rgba(0,0,0,0.25);
    overflow: hidden;
  }
  .billboard-shapes { position: absolute; inset: 0; }
  .brand-name {
    position: absolute; left: 48px; top: 20px;
    font-weight: 800; font-size: 50px; letter-spacing: 2px;
    color: var(--brand-blue); line-height: 1;
  }
  .headline {
    position: absolute; left: 48px; top: 98px;
    font-family: "Oswald", "Arial Narrow", sans-serif;
    font-weight: 700; font-style: italic;
    font-size: 44px; line-height: 50px;
    color: var(--white); text-transform: uppercase; letter-spacing: 0.3px;
  }
  .tagline {
    position: absolute; left: 48px; top: 225px;
    font-weight: 700; font-size: 13.5px; color: var(--ink);
  }
  .cta-web-label {
    position: absolute; left: 48px; top: 268px;
    font-weight: 700; font-size: 15px; line-height: 19px;
    color: var(--white); text-transform: uppercase;
  }
  .cta-web-url {
    position: absolute; left: 245px; top: 273px;
    font-weight: 700; font-size: 23px; color: var(--white);
  }
  .cta-web-url .accent { color: var(--orange); }
  .cta-call-label {
    position: absolute; left: 590px; top: 270px;
    font-weight: 700; font-size: 14.5px; line-height: 18px;
    color: var(--white); text-transform: uppercase;
  }
  .cta-call-icon { position: absolute; left: 688px; top: 272px; }
  .cta-call-number {
    position: absolute; left: 730px; top: 268px;
    font-weight: 700; font-size: 33px; line-height: 40px; color: var(--white);
    letter-spacing: 0.5px;
  }
</style>
</head>
<body>
  <section class="billboard">
    <svg class="billboard-shapes" width="1105" height="322" viewBox="0 0 1105 322">
      <defs>
        <linearGradient id="band-blue" x1="0" x2="1">
          <stop offset="0" stop-color="var(--band-blue-dark)"/>
          <stop offset="1" stop-color="var(--brand-blue)"/>
        </linearGradient>
        <linearGradient id="bar-navy" x1="0" x2="1">
          <stop offset="0" stop-color="var(--navy)"/>
          <stop offset="1" stop-color="var(--navy-mid)"/>
        </linearGradient>
        <linearGradient id="bar-orange" x1="0" x2="1">
          <stop offset="0" stop-color="var(--orange-dark)"/>
          <stop offset="1" stop-color="var(--orange)"/>
        </linearGradient>
        <linearGradient id="photo-tone" x1="0" y1="1" x2="1" y2="0">
          <stop offset="0" stop-color="var(--photo-deep)"/>
          <stop offset="0.45" stop-color="var(--photo-mid)"/>
          <stop offset="1" stop-color="var(--photo-light)"/>
        </linearGradient>
      </defs>
      <rect class="panel-white" width="1105" height="322" fill="var(--white)"/>
      <polygon class="photo-area" role="img"
        aria-label="Photo of a hand pressing a button on a business desk phone, overlaid with connected communication icons"
        points="690,0 1105,0 1105,252 575,252" fill="url(#photo-tone)"/>
      <polygon class="photo-shade" points="660,70 720,70 640,252 575,252" fill="var(--navy-mid)" opacity="0.85"/>
      <line class="accent-stripe-blue" x1="650" y1="0" x2="626" y2="46" stroke="var(--brand-blue)" stroke-width="3"/>
      <line class="accent-stripe-orange" x1="662" y1="0" x2="636" y2="50" stroke="var(--orange-dark)" stroke-width="3"/>
      <polygon class="headline-band" points="0,88 672,88 617,212 0,212" fill="url(#band-blue)"/>
      <polygon class="footer-web" points="0,256 576,256 542,322 0,322" fill="url(#bar-navy)"/>
      <polygon class="footer-call" points="580,256 1105,256 1105,322 546,322" fill="url(#bar-orange)"/>
    </svg>

    <div class="brand-name">Brivoqua</div>
    <h1 class="headline">Elevate your business with<br>next-gen IT and VOIP services</h1>
    <p class="tagline">Innovative IT and VOIP Solutions Tailored for Your Business Success.</p>

    <p class="cta-web-label">Transform your<br>tech today at</p>
    <p class="cta-web-url">www.<span class="accent">brivoqua</span>.com</p>

    <p class="cta-call-label">Call us<br>today</p>
    <svg class="cta-call-icon" width="34" height="34" viewBox="0 0 34 34" aria-hidden="true">
      <circle cx="17" cy="17" r="16" fill="var(--white)"/>
      <path d="M11.5 9.5c1-.8 2-.6 2.6.4l1.5 2.6c.5.9.3 1.8-.5 2.4l-1 .7c.8 2 2.3 3.6 4.3 4.4l.7-1c.6-.8 1.5-1 2.4-.5l2.6 1.5c1 .6 1.2 1.6.4 2.6l-1 1.2c-1 1.1-2.7 1.4-4.2.7-4.2-1.9-7.3-5-9.2-9.2-.7-1.5-.4-3.2.7-4.2z" fill="var(--brand-blue)"/>
      <path d="M19 9.5a6 6 0 0 1 5.5 5.5M19 12.3a3.2 3.2 0 0 1 2.7 2.7" stroke="var(--brand-blue)" stroke-width="1.5" fill="none" stroke-linecap="round"/>
    </svg>
    <p class="cta-call-number">(352) 555-0147</p>
  </section>
</body>
</html>
```